Business Card for Coastal Tundrabridge Advisory

We need a business card for Coastal Tundrabridge Advisory. The company website address is provided below. The company logo is attached. We provide specialized permafrost services to the mining, transportation, and oil & gas industries. The card should be prepared for:
Matthias Korhonen, PhD.
Coastal Tundrabridge Advisory
PO Box 418259
Quillwater, Alaska 99642
Direct: +1-907-555-0143
Email: mkorhonen@tundrabridgeadvisory.example
Website: www.coastaltundrabridgeadvisory.example

```html
<!DOCTYPE html>
<html lang="en">
<head>
<meta charset="utf-8">
<title>Coastal Tundrabridge Advisory – Business Card</title>
<link rel="stylesheet" href="https://fonts.googleapis.com/css2?family=Montserrat:wght@400;500;600;700&display=swap">
<style>
  :root {
    --backdrop: #d9d4cc;
    --card-white: #ffffff;
    --ink: #141c24;
    --navy: #111a23;
    --paper-text: #ffffff;
    --shadow: rgba(0,0,0,0.35);
  }
  * { box-sizing: border-box; margin: 0; padding: 0; }
  html, body { width: 900px; height: 1200px; overflow: hidden; }
  body {
    background: var(--backdrop);
    font-family: "Montserrat", Arial, sans-serif;
    position: relative;
  }
  .card {
    position: absolute;
    left: 80px;
    width: 742px;
    height: 440px;
    border-radius: 22px;
    overflow: hidden;
    box-shadow: 0 10px 24px var(--shadow);
  }
  .card-front { top: 131px; background: var(--card-white); color: var(--ink); }
  .card-back { top: 639px; background: var(--navy); }

  .brand-name {
    font-family: "Montserrat", Arial, sans-serif;
    font-weight: 600;
    text-transform: uppercase;
    letter-spacing: 0.06em;
    white-space: nowrap;
  }
  .card-front .brand-name {
    position: absolute;
    right: 38px;
    top: 66px;
    font-size: 22px;
    color: var(--ink);
  }
  .card-back .brand-name {
    position: absolute;
    left: 0; right: 0;
    top: 200px;
    text-align: center;
    font-size: 34px;
    color: var(--paper-text);
  }

  .holder { position: absolute; left: 25px; top: 236px; }
  .holder-name { font-size: 22px; font-weight: 700; line-height: 1.2; }
  .holder-role { font-size: 16px; font-weight: 400; margin-top: 3px; }
  .divider {
    position: absolute; left: 25px; right: 27px; top: 291px;
    height: 2px; background: var(--ink);
  }

  .contact-list { position: absolute; left: 27px; top: 312px; list-style: none; }
  .contact-item {
    display: flex; align-items: center; gap: 12px;
    font-size: 15.5px; height: 30.5px;
  }
  .contact-item svg { width: 17px; height: 17px; fill: var(--ink); flex: none; }

  .footer-band { position: absolute; left: 0; bottom: 0; width: 742px; height: 54px; }
  .footer-band path { fill: var(--navy); }
  .address {
    position: absolute; left: 490px; top: 394px;
    color: var(--paper-text); font-size: 16px; line-height: 20px;
  }
</style>
</head>
<body>

<section class="card card-front" aria-label="Card front">
  <div class="brand-name">Coastal Tundrabridge Advisory</div>

  <div class="holder">
    <div class="holder-name">Matthias Korhonen, PhD.</div>
    <div class="holder-role">Managing Director</div>
  </div>
  <div class="divider"></div>

  <ul class="contact-list">
    <li class="contact-item">
      <svg viewBox="0 0 24 24" aria-hidden="true"><path d="M6.6 10.8a15.1 15.1 0 0 0 6.6 6.6l2.2-2.2c.3-.3.7-.4 1-.2 1.1.4 2.3.6 3.6.6.6 0 1 .4 1 1V20c0 .6-.4 1-1 1C10.6 21 3 13.4 3 4c0-.6.4-1 1-1h3.5c.6 0 1 .4 1 1 0 1.3.2 2.5.6 3.6.1.3 0 .7-.2 1z"/></svg>
      <span>+1-907-555-0143</span>
    </li>
    <li class="contact-item">
      <svg viewBox="0 0 24 24" aria-hidden="true"><path d="M3 5h18v14H3z M3 5l9 7 9-7" stroke="#fff" stroke-width="1.6"/></svg>
      <span>mkorhonen@tundrabridgeadvisory.example</span>
    </li>
    <li class="contact-item">
      <svg viewBox="0 0 24 24" aria-hidden="true"><circle cx="12" cy="12" r="10"/><path d="M2 12h20M12 2c3 3 3 17 0 20M12 2c-3 3-3 17 0 20" stroke="#fff" stroke-width="1.3" fill="none"/></svg>
      <span>www.coastaltundrabridgeadvisory.example</span>
    </li>
  </ul>

  <svg class="footer-band" viewBox="0 0 742 54" aria-hidden="true">
    <path d="M0 30 H433 L412 54 H0 Z"/>
    <path d="M472 0 H742 V54 H422 Z"/>
  </svg>
  <div class="address">
    <div>PO Box 418259</div>
    <div>Quillwater, Alaska 99642</div>
  </div>
</section>

<section class="card card-back" aria-label="Card back">
  <div class="brand-name">Coastal Tundrabridge Advisory</div>
</section>

</body>
</html>
```